Web Design Project

We wish to create a web based logistics exchange for heavy machinery and equipment catering to the mining, oil, gas and infrastructure industries. Customers interested in shipping equipment can post a load on the site and this would then be auctioned off through an online auction to prospective transport providers.Payments would be through direct bank transfer,pelko, quorvantix etc.
Both shippers and transport providers gain access via membership.
When a load is posted it would appear on the map indicating its location.Transport providers click on the icon of this map to access information of the pick up and delivery details as well as the load description.
The site would also have links to transport departments and equipment specification sites.
Advertising and merchandising are the other areas of revenue through the site

Target Market(s)

Shippers from Machinery Auction centres and Transport companies

Industry/Entity Type

Catering

Requirements
Must have
• The Logo of the company. The file is attached.

```html
<!DOCTYPE html>
<html lang="en">
<head>
<meta charset="utf-8">
<title>Loadmarra – Heavy Haulage Exchange</title>
<link rel="stylesheet" href="https://fonts.googleapis.com/css2?family=Source+Sans+3:ital,wght@0,400;0,600;1,400&display=swap">
<style>
:root{
  --blue-dark:#0a6fbf;
  --blue:#1a8fdc;
  --blue-light:#2fb4f0;
  --sky:#35c0f5;
  --orange:#f7901e;
  --orange-dark:#e86f0c;
  --green:#7cc043;
  --green-dark:#5ea82f;
  --hero:#1d1f22;
  --text-blue:#1b7bc4;
  --white:#ffffff;
  --panel-grey:#f2f5f7;
}
*{box-sizing:border-box;margin:0;padding:0}
html,body{width:755px;height:1200px;overflow:hidden}
body{position:relative;font-family:"Source Sans 3",Arial,sans-serif;background:#fff;color:var(--white)}
.abs{position:absolute}
.header{left:0;top:0;width:755px;height:86px;background:linear-gradient(var(--blue),var(--blue-dark))}
.header-stripe{left:0;top:88px;width:755px;height:20px;background:linear-gradient(var(--sky),#18a4e6)}
.brand{left:98px;top:52px;display:flex;align-items:center;gap:6px;font-size:20px;font-weight:600}
.brand i{width:14px;height:14px;background:#fff;display:block}
.phone{left:568px;top:10px;font-size:11px;font-weight:600;display:flex;gap:4px;align-items:center}
.account{left:528px;top:27px;width:128px;height:17px;border:1px solid #5cc6f5;background:#1e9ae6;display:flex;justify-content:space-around;font-size:8px;line-height:15px}
.nav{left:265px;top:62px;width:391px;height:25px;background:linear-gradient(#25a9ef,#1590df);border:1px solid #60c8f5;display:flex;font-size:11px;line-height:23px}
.nav span{padding:0 8px;border-right:1px solid #58bff0}
.nav span:first-child{background:#0f7fcc}
.nav span:last-child{border:0}
.hero{left:0;top:110px;width:755px;height:220px;background:radial-gradient(circle at 60% 40%,#34373b,var(--hero))}
.hero-photo{left:100px;top:96px;width:244px;height:196px;background:linear-gradient(#4b7fbf 0%,#b7cde4 45%,#7b6e5c 60%,#4a4a4a 100%);border:3px solid #e9eef2;transform:perspective(600px) rotateY(8deg) rotateZ(1deg)}
.hero-title{left:396px;top:146px;font-size:26px;line-height:29px;font-weight:400}
.hero-text{left:396px;top:218px;width:260px;font-size:11px;line-height:11.5px}
.btn-orange{left:428px;top:266px;width:70px;height:17px;background:linear-gradient(#fba739,var(--orange-dark));border-radius:2px;font-size:9px;text-align:center;line-height:17px}
.content{left:0;top:330px;width:755px;height:498px;background:repeating-linear-gradient(45deg,#f4f4f4 0 2px,#fff 2px 4px)}
.content-inner{left:98px;top:330px;width:560px;height:498px;background:#fff}
.card{width:176px;height:222px;top:358px;border-radius:3px;overflow:hidden}
.card-head{height:66px;padding:8px 7px;font-size:14px;position:relative}
.card-head .wave{position:absolute;left:0;bottom:0}
.card-item{padding:4px 11px;font-size:9.5px;line-height:10px;border-top:1px solid rgba(255,255,255,.6);position:relative}
.auction{left:98px;background:var(--blue-light)}
.auction .card-head{background:linear-gradient(#42c2f7,#2aa6ec)}
.auction .card-item{height:77px}
.news{left:290px;background:var(--orange)}
.news .card-head{background:linear-gradient(#fba24a,#f7861c)}
.news .card-item{height:39px;padding-top:5px}
.news .card-item .txt{display:block;width:118px}
.project{left:482px;background:var(--green)}
.project .card-head{background:linear-gradient(#9ad262,#79bf42)}
.meta{font-size:8px;display:flex;justify-content:flex-end;gap:14px;font-style:italic;color:#0a4f8a}
.more{position:absolute;right:9px;bottom:7px;color:#8a3d00;font-style:italic;font-size:8.5px;line-height:10px}
.icon-ph{position:absolute;right:6px;top:4px;width:54px;height:54px;border-radius:6px}
.form-row{display:flex;align-items:center;font-size:8px;line-height:7px;font-weight:600;padding:0 10px;height:20px}
.form-row b{width:54px;font-weight:600}
.form-row .field{width:70px;height:11px;background:#fff;border:1px solid #cde6b4;color:#bbb;font-size:6px;line-height:10px;padding-left:4px;font-style:italic}
.form-row .post{margin-left:11px;width:26px;height:12px;background:#f1f6e9;color:#3d6d16;font-size:7px;line-height:12px;text-align:center;border:1px solid #cfe2b7}
.form-big{height:34px}
.form-big .field{height:26px}
.about-title{left:110px;top:610px;color:var(--text-blue);font-size:15px;font-weight:400}
.about-text{left:110px;top:628px;width:344px;color:var(--text-blue);font-size:10.2px;line-height:12.8px}
.gallery-title{left:110px;top:703px;color:var(--text-blue);font-size:15px;font-weight:400}
.thumb{top:722px;width:80px;height:56px;border:1px solid #2a6ea8}
.quote{left:494px;top:624px;width:156px;height:58px;background:var(--panel-grey);border:1px solid #e3e7ea;color:var(--text-blue);font-size:10.3px;line-height:12.8px;padding:9px 8px}
.person{left:588px;top:672px;width:70px;height:114px;background:linear-gradient(#d9dde2,#2b2f38)}
.partners{left:110px;top:792px;width:548px;height:34px;border-top:1px solid #e4e4e4;display:flex;align-items:center;justify-content:space-between;color:#333;font-size:7px;font-weight:600}
.badge{width:36px;height:20px;background:#555;border-radius:50% 50% 8px 8px}
.footer-mid{left:0;top:828px;width:755px;height:160px;background:linear-gradient(#1c8ad6,#0f73c0)}
.col-title{top:840px;font-size:15px;color:#bfe4ff;font-weight:400}
.bp-item{left:110px;width:164px;height:38px;border-bottom:1px solid #4aa0dc;font-size:11px;line-height:13px;padding-top:6px;position:absolute}
.bp-item em{position:absolute;right:12px;top:20px;font-style:normal;font-size:9px;font-weight:600;color:#bfe4ff}
.article{left:302px;width:170px;height:64px;border-bottom:1px solid #4aa0dc}
.article .num{position:absolute;left:10px;top:4px;font-size:32px}
.article .txt{position:absolute;left:40px;top:0;font-size:11px;line-height:13px;width:126px}
.article .full{position:absolute;right:0;top:50px;font-size:8.5px;font-style:italic;color:#bfe4ff}
.input{left:494px;width:163px;height:30px;background:#fff;border:1px solid #8cc6ee;color:#888;font-size:10px;font-style:italic;padding:8px 11px}
.btn-post{left:597px;top:945px;width:60px;height:20px;background:linear-gradient(#35b6f5,#158fdc);border:1px solid #7ccff8;font-size:10px;text-align:center;line-height:18px}
.stats-band{left:0;top:990px;width:755px;height:106px;background:linear-gradient(#106cb8,#0d62aa)}
.stats{left:113px;top:1012px;font-size:14px;line-height:19.5px}
.sitemap{left:342px;top:1006px;width:108px;height:70px;background:linear-gradient(135deg,#ffffff,#e1e6ea)}
.sitemap-label{left:378px;top:1078px;font-size:8.5px;font-weight:600}
.brand-foot{left:520px;top:1030px;font-size:17px;display:flex;align-items:center;gap:7px;letter-spacing:.5px}
.brand-foot i{width:14px;height:14px;background:#fff;display:block}
.bottom{left:0;top:1098px;width:755px;height:102px;background:linear-gradient(#1b8ad7,#1877c7)}
.follow{left:110px;top:1146px;font-size:10.5px}
.social{left:110px;top:1163px;display:flex;gap:5px}
.social span{width:24px;height:24px;font-size:6px;text-align:center;line-height:24px;font-weight:600;display:block;border-radius:2px}
.links{left:310px;top:1108px;font-size:10.5px;line-height:13px}
.links-cols{display:flex;gap:16px}
.contact{left:494px;top:1110px;font-size:10.5px;line-height:12.8px}
</style>
</head>
<body>
<header>
  <div class="abs header"></div>
  <div class="abs header-stripe"></div>
  <div class="abs brand"><i></i>Loadmarra</div>
  <div class="abs phone">
    <svg width="12" height="12" viewBox="0 0 12 12"><rect width="12" height="12" rx="2" fill="#fff"/><path d="M3.5 2.5l1.5 0 .7 2-1 .8a5 5 0 0 0 2.5 2.5l.8-1 2 .7v1.5c-4 .5-7-2.5-6.5-6.5z" fill="#1a8fdc"/></svg>
    1400 XXX XXX
  </div>
  <div class="abs account"><span>Login</span><span>Register</span><span>Help</span></div>
  <nav class="abs nav"><span>Home</span><span>Services</span><span>Buying</span><span>Selling</span><span>Online Bid</span><span>Auction Results</span></nav>
</header>

<section>
  <div class="abs hero"></div>
  <div class="abs hero-photo" role="img" aria-label="Heavy haulage truck carrying mining machinery on an outback road"></div>
  <h1 class="abs hero-title">This is Photoshop's<br>version&nbsp; of Lorem Ipsum.</h1>
  <p class="abs hero-text">Proin gravida nibh vel velit auctor aliquet. Aenean sollicitudin, lorem quis bibendum auctor, nisi elit consequat ipsum.</p>
  <div class="abs btn-orange">View more</div>
</section>

<main>
  <div class="abs content"></div>
  <div class="abs content-inner"></div>

  <div class="abs card auction">
    <div class="card-head">Online Auction
      <div class="icon-ph" role="img" aria-label="Auction gavel" style="background:linear-gradient(#8a5a2a,#c98f4e);width:44px;height:26px;top:26px;right:20px"></div>
      <svg class="wave" width="176" height="20"><path d="M0 20V10Q60-2 110 10T176 6V20z" fill="#fff"/></svg>
    </div>
    <div class="card-item">This is Photoshop's version&nbsp; of Lorem Ipsum. Proin gravida nibh vel velit auctor aliquet. Aenean sollicitudin, lorem quis<br><span style="font-size:8px">contact - 808080808</span><div class="meta"><span>View Detail</span><span>Bid Now</span></div></div>
    <div class="card-item">This is Photoshop's version&nbsp; of Lorem Ipsum. Proin gravida nibh vel velit auctor aliquet. Aenean sollicitudin, lorem.<br><span style="font-size:8px">contact - 8080808080</span><div class="meta"><span>View Detail</span><span>Bid Now</span></div></div>
  </div>

  <div class="abs card news">
    <div class="card-head">Recent news
      <div class="icon-ph" role="img" aria-label="News envelope icon" style="background:linear-gradient(135deg,#f4f4f4,#9a9a9a)"></div>
      <svg class="wave" width="176" height="20"><path d="M0 20V10Q60-2 110 10T176 6V20z" fill="#fff"/></svg>
    </div>
    <div class="card-item"><span class="txt">This is Photoshop's version&nbsp; of Lorem Ipsum.</span><span class="more">View more</span></div>
    <div class="card-item"><span class="txt">Lorem Ipsum is simply dummy text of the printing.</span><span class="more">View more</span></div>
    <div class="card-item"><span class="txt">This is Photoshop's version&nbsp; of Lorem Ipsum.</span><span class="more">View more</span></div>
    <div class="card-item"><span class="txt">This is Photoshop's version&nbsp; of Lorem Ipsum.</span><span class="more">View more</span></div>
  </div>

  <div class="abs card project">
    <div class="card-head">Post Project
      <div class="icon-ph" role="img" aria-label="Upload arrow icon" style="background:linear-gradient(135deg,#c8f0a0,#3f9a2a)"></div>
      <svg class="wave" width="176" height="20"><path d="M0 20V10Q60-2 110 10T176 6V20z" fill="#fff"/></svg>
    </div>
    <div style="padding-top:6px;background:var(--green-dark)">
      <div class="form-row"><b>Sourse<br>Station</b><span class="field">test here text</span><span class="post">Post</span></div>
      <div class="form-row"><b>Destination<br>Station</b><span class="field">test here text</span><span class="post">Post</span></div>
      <div class="form-row"><b>Load<br>Details</b><span class="field">test here text</span><span class="post">Post</span></div>
      <div style="height:4px;background:#fff"></div>
    </div>
    <div style="padding-top:6px">
      <div class="form-row form-big"><b>Project<br>Holder<br>Information</b><span class="field"></span><span class="post">Post</span></div>
      <div class="form-row form-big"><b>Extra<br>comment</b><span class="field"></span><span class="post">Post</span></div>
    </div>
  </div>

  <h2 class="abs about-title">About Loadmarra</h2>
  <p class="abs about-text">Lorem Ipsum is simply dummy text of the printing and typesetting industry. Lorem Ipsum has been the industry's standard dummy text ever since the 1500s, when an unknown printer took a galley of type and scrambled it to make a type specimen book. It has survived not only five centuries, but also the leap into electronic typesetting.</p>
  <h2 class="abs gallery-title">Photo Gallery</h2>
  <div class="abs thumb" style="left:110px;background:linear-gradient(#7fb4e6,#c2a54a 70%,#555)" role="img" aria-label="Low loader truck with yellow machinery"></div>
  <div class="abs thumb" style="left:206px;background:linear-gradient(#b8c6d4,#5b6670 70%,#d8dde2)" role="img" aria-label="Heavy transport in snow"></div>
  <div class="abs thumb" style="left:302px;background:linear-gradient(#8aa8c8,#d9a92a 55%,#6d5b3b)" role="img" aria-label="Truck hauling a yellow bulldozer"></div>
  <div class="abs thumb" style="left:398px;background:linear-gradient(#e9ecef,#2c3440)" role="img" aria-label="Business team"></div>

  <div class="abs quote">Lorem Ipsum is simply dummy text of the printing and typesetting industry.</div>
  <svg class="abs" style="left:590px;top:681px" width="22" height="14"><path d="M0 0H20L8 13z" fill="#f2f5f7"/></svg>
  <div class="abs person" role="img" aria-label="Consultant in a suit"></div>

  <div class="abs partners">
    <span>Roadhaul</span><span class="badge"></span><span>Tessan Freight</span><span>Kurrvik Cabs</span><span class="badge"></span><span>Onward Hauling</span><span>Mbeka Group</span><span>Roadhaul</span><span class="badge"></span><span>Tessan Freight</span>
  </div>
</main>

<footer>
  <div class="abs footer-mid"></div>
  <h3 class="abs col-title" style="left:113px">Beneficiary Projects</h3>
  <div class="bp-item" style="top:860px">Lorem Ipsum is simply dummy text of the printing<em>GO</em></div>
  <div class="bp-item" style="top:898px">Lorem Ipsum is simply dummy text of the printing<em>GO</em></div>
  <div class="bp-item" style="top:936px">Lorem Ipsum is simply dummy text of the printing<em>GO</em></div>

  <h3 class="abs col-title" style="left:302px">Our Atricles</h3>
  <div class="abs article" style="top:864px"><span class="num">1</span><span class="txt">Lorem Ipsum is simply dummy text of the print-ing and typesetting</span><span class="full">full article</span></div>
  <div class="abs article" style="top:928px;border:0"><span class="num">2</span><span class="txt">Lorem Ipsum is simply dummy text of the print-ing and typesetting</span><span class="full">full article</span></div>

  <h3 class="abs col-title" style="left:494px">Consulting Corner</h3>
  <div class="abs input" style="top:869px">post your problems here</div>
  <div class="abs input" style="top:907px">Yourgoodname@email.com</div>
  <div class="abs" style="left:494px;top:954px;width:163px;height:1px;background:#4aa0dc"></div>
  <div class="abs btn-post">Post</div>

  <div class="abs stats-band"></div>
  <div class="abs stats">078&nbsp; Project Auctioned<br>213&nbsp; Projects Completed<br>033&nbsp; Open Projects</div>
  <div class="abs sitemap" role="img" aria-label="Site map diagram with location pins"></div>
  <div class="abs sitemap-label">sitemap</div>
  <div class="abs brand-foot"><i></i>LOADMARRA</div>

  <div class="abs bottom"></div>
  <div class="abs follow">Follow us &amp; stay connected with us</div>
  <div class="abs social">
    <span style="background:#3b5ba0">Kivo</span><span style="background:#f57d00">Penla</span><span style="background:#35b3e8">Chirra</span><span style="background:#f39a1d">Feedo</span><span style="background:#1b3f8f">Rumba</span><span style="background:#d8262a">Vidda</span>
  </div>
  <div class="abs links">Hot Links
    <div class="links-cols"><div>* Home<br>* Buyers<br>* Sellers<br>* FAQ</div><div>* Online bidding<br>* Auctioned Projects<br>* Our Services<br>* Help</div></div>
  </div>
  <div class="abs contact">Contact Address<br>Lorem Ipsum is&nbsp; dummy printing<br>typesetting industry.<br>Call us - 1400 000 XXX<br><span style="font-size:9px">Mail us - company @mailhostly.com</span></div>
</footer>
</body>
</html>
```